New website for a business that provides Calmpath Support

A new website that details the services that are provided around Calmpath Support for people with a disability through QPKV. There also needs to incorporate an about us and a staff page, Plus a referral form that is a google doc.
The business already has a web address that needs to be tailored.
Soft colours are preferred.
Do not have lots of pictures, keep them minimal.
A logo for the business is also needed to be incorporated, and this is a separate project that can be awarded to the website winner.
Website needs to be able to be used on WIX who will be the host for the design.

Target Market(s)

QPKV clients requiring behaviour support clician

Industry/Entity Type

Clinical behaviour support and analysis

Colors
00AB8E
00BBA5
67D7C9
C6EFE9
E9F9F6

Requirements
Must have
• Soft colours, preferable pale turquoise, minimal pictures, clean, sophisticated and classical look

```html
<!DOCTYPE html>
<html lang="en">
<head>
<meta charset="utf-8">
<title>Calmpath Support — Behaviour Support Services</title>
<link rel="stylesheet" href="https://fonts.googleapis.com/css2?family=Montserrat:wght@400;500;600;700;800&display=swap">
<style>
:root{
  --teal:#00ab8e;
  --teal-2:#00bba5;
  --teal-3:#67d7c9;
  --mint:#d6f2ed;
  --mint-pale:#e9f9f6;
  --ink:#222222;
  --body:#6b6b6b;
  --dark:#2b2b2b;
  --line:#1f2a3a;
  --grey-bg:#f1f1f1;
  --white:#ffffff;
}
*{margin:0;padding:0;box-sizing:border-box}
html,body{width:1200px;height:3404px;overflow:hidden}
body{font-family:'Montserrat',sans-serif;color:var(--ink);background:var(--white);position:relative}
.abs{position:absolute}

/* buttons */
.btn{position:absolute;display:flex;align-items:center;padding-left:18px;font-size:11.5px;font-weight:600;letter-spacing:.3px;color:var(--white);text-transform:uppercase}
.btn::before{content:"";position:absolute;left:0;top:0;bottom:0;right:10px;background:var(--bg);clip-path:polygon(0 0,100% 0,calc(100% - 8px) 100%,0 100%);z-index:-1}
.btn::after{content:"";position:absolute;right:1px;top:0;width:5px;height:100%;background:var(--bar);transform:skewX(-12deg)}
.btn span{position:relative}
.btn-dark{--bg:var(--dark);--bar:var(--teal)}
.btn-teal{--bg:var(--teal);--bar:var(--dark)}
.btn{z-index:1}

/* header */
.topbar{left:601px;top:0;width:599px;height:36px;background:var(--teal);clip-path:polygon(0 0,100% 0,100% 100%,34px 100%);display:flex;align-items:center;gap:38px;padding-left:72px;color:var(--white);font-size:15px}
.topbar div{display:flex;align-items:center;gap:10px}
.brand{left:111px;top:28px;font-size:30px;font-weight:700;line-height:35px;color:var(--ink);letter-spacing:.3px}
.nav{left:432px;top:70px;display:flex;gap:29px;font-size:11.5px;font-weight:500;color:var(--ink)}

/* hero */
.hero{left:0;top:122px;width:1200px;height:427px;background:linear-gradient(90deg,#3fb9a3 0%,#57b99a 35%,#8fbf84 60%,#9c8f6a 80%,#b89a7c 100%)}
.hero-text{left:110px;top:220px;color:var(--white)}
.hero-text h1{font-size:44px;line-height:60px;font-weight:700;letter-spacing:.5px}
.hero-text h1 .thin{font-weight:400}
.hero-text p{font-size:32px;font-weight:400;margin-top:6px}

/* about */
.about-frame{left:348px;top:630px;width:740px;height:418px;border:2.5px solid var(--line);border-left:none;border-bottom:none}
.about-frame-b{left:584px;top:1045px;width:504px;height:2.5px;background:var(--line)}
.about-frame-b2{left:348px;top:630px;width:2.5px;height:50px;background:var(--line)}
.about-frame-r{left:1086px;top:630px;width:2.5px;height:418px;background:var(--line)}
.about-frame-l{left:546px;top:1045px;width:52px;height:2.5px;background:var(--line)}
.about-img{left:111px;top:681px;width:435px;height:430px;background:linear-gradient(135deg,#7fa05b 0%,#b2b48a 40%,#d8c3a8 60%,#6fbf8a 100%)}
.about-title{left:611px;top:690px;font-size:40px;font-weight:700}
.about-title span,.h2 span{color:var(--teal)}
.about-copy{left:610px;top:754px;width:450px;font-size:15px;line-height:28.3px;color:var(--body)}

/* why */
.why-band{left:0;top:1300px;width:1200px;height:416px;background:var(--mint)}
.why-title{left:111px;top:1256px;font-size:40px;font-weight:700;line-height:49px}
.why-title span{color:var(--teal)}
.card{position:absolute;width:271px;height:213px;background:var(--white);border:1px solid #ececec;padding:18px 19px}
.card.active{background:var(--teal);border-color:var(--teal);color:var(--white)}
.card .ico{position:relative;width:60px;height:44px}
.card .ico i{position:absolute;left:28px;top:3px;width:38px;height:38px;border-radius:50%;background:var(--mint-pale)}
.card.active .ico i{background:rgba(255,255,255,.25);left:3px}
.card .ico svg{position:relative}
.card h3{font-size:15.5px;font-weight:600;margin-top:19px}
.card p{font-size:14px;line-height:24px;color:var(--body);margin-top:19px;padding-left:1px}
.card.active p{color:var(--white)}

/* team */
.h2{position:absolute;left:0;width:1200px;text-align:center;font-size:40px;font-weight:700}
.member{position:absolute;top:1903px;width:227px;height:331px;display:flex;flex-direction:column;justify-content:flex-end;padding:0 0 32px 30px;color:var(--white)}
.member h4{font-size:15px;font-weight:700}
.member p{font-size:12.5px;margin-top:5px}

/* blog */
.blog-bg{left:0;top:2383px;width:1200px;height:731px;background:var(--grey-bg)}
.post-main{left:111px;top:2545px;width:556px;height:396px;background:var(--white);padding:13px}
.post-main .photo{height:173px;background:linear-gradient(90deg,#8a8270 0%,#c8b79a 45%,#6b5a4a 70%,#a9b0b5 100%)}
.meta{display:flex;align-items:center;gap:8px;font-size:15px;color:#a7a7a7}
.post-main .meta{margin:26px 0 0 18px}
.post-main h3{font-size:17.5px;font-weight:600;line-height:28px;margin:12px 0 0 18px}
.post-main p{font-size:15px;line-height:28px;color:var(--body);margin:10px 0 0 18px}
.post-sm{position:absolute;left:675px;width:413px;height:121px;background:var(--white);display:flex;padding:8px}
.post-sm .photo{width:141px;height:106px;flex:none}
.post-sm .txt{padding:14px 0 0 19px;font-size:15px;line-height:24px;color:var(--body)}
.post-sm .meta{margin-top:9px}

/* footer */
.footer{left:0;top:3114px;width:1200px;height:290px;background:var(--dark);color:var(--white)}
.f-brand{left:111px;top:3158px;font-size:30px;font-weight:700;line-height:35px;color:var(--white)}
.social{left:111px;top:3255px;display:flex;gap:11px}
.social span{width:34px;height:34px;border:1.5px solid var(--white);border-radius:50%}
.f-h{font-size:15.5px;font-weight:600;letter-spacing:.2px}
.f-col{font-size:14px;line-height:26px}
.f-row{display:flex;gap:14px;align-items:flex-start}
.email-in{left:853px;top:3199px;width:235px;height:52px;background:var(--white);color:#888;font-size:14px;padding:19px 0 0 19px}
.copy{left:0;top:3363px;width:1200px;text-align:center;font-size:15px}
</style>
</head>
<body>

<!-- header -->
<div class="abs topbar">
  <div><svg width="15" height="15" viewBox="0 0 24 24"><path fill="#fff" d="M6.6 10.8a15 15 0 0 0 6.6 6.6l2.2-2.2c.3-.3.7-.4 1-.2 1.1.4 2.3.6 3.6.6.6 0 1 .4 1 1V20c0 .6-.4 1-1 1A17 17 0 0 1 3 4c0-.6.4-1 1-1h3.5c.6 0 1 .4 1 1 0 1.3.2 2.5.6 3.6.1.3 0 .7-.2 1z"/></svg>+1800-555-0142</div>
  <div><svg width="15" height="12" viewBox="0 0 24 18"><rect x="1" y="1" width="22" height="16" fill="#fff"/><path d="M1 1l11 9 11-9" stroke="#00ab8e" stroke-width="2" fill="none"/></svg>hello@calmpathsupport.com</div>
</div>
<div class="abs brand">CALMPATH<br>SUPPORT</div>
<nav class="abs nav"><span>HOME</span><span>ABOUT</span><span>SERVICES</span><span>WHY CHOOSE US</span><span>STAFF</span><span>CONTACT</span></nav>
<div class="btn btn-dark" style="left:946px;top:57px;width:142px;height:43px"><span>Request Quote</span></div>

<!-- hero -->
<div class="abs hero" role="img" aria-label="Photo of a young child blowing bubbles on a sunny lawn"></div>
<div class="abs hero-text">
  <h1>PERSONALIZED CARE,<br><span class="thin">LASTING IMPACT</span></h1>
  <p>QPKV Behavior Analysis Services</p>
</div>
<div class="btn btn-dark" style="left:115px;top:414px;width:142px;height:45px;padding-left:34px"><span>Referral</span></div>

<!-- about -->
<div class="abs" style="left:348px;top:630px;width:740px;height:2.5px;background:var(--line)"></div>
<div class="abs about-frame-b2"></div>
<div class="abs about-frame-r"></div>
<div class="abs about-frame-b"></div>
<div class="abs about-frame-l"></div>
<div class="abs about-img" role="img" aria-label="Photo of a carer and a smiling client playing with a dog in a garden"></div>
<h2 class="abs about-title">ABOUT <span>US</span></h2>
<p class="abs about-copy">Lorem ipsum dolor sit amet, consectetur adipiscing elit, sed do eiusmod tempor incididunt ut labore et dolore magna aliqua. Quis ipsum suspendisse ultrces gravida. Risus commodo viver ra maecenas accumsan lacus vel facilisis. Lorem ipsum dolor sit amet, consectetur adipisc ing elit, sed do eiusmod tempor incididunt ut labore et dolore magna aliqua. Quis ipsuspendis se ultrices gravida. Risus commodo viverra maeas accumsan lacus vel.</p>
<div class="btn btn-teal" style="left:599px;top:1015px;width:125px;height:44px"><span>Learn More</span></div>

<!-- why choose us -->
<div class="abs why-band"></div>
<h2 class="abs why-title">WHY<br><span>CHOOSE US</span></h2>

<div class="card" style="left:546px;top:1200px">
  <div class="ico"><i></i><svg width="30" height="34" viewBox="0 0 30 34" fill="none" stroke="#333" stroke-width="1.6"><path d="M15 2l12 4v9c0 8-5 14-12 17C8 29 3 23 3 15V6z"/><path d="M15 6l8 3v6c0 5-3 10-8 12-5-2-8-7-8-12V9z"/><path d="M11 16l3 3 6-6"/></svg></div>
  <h3>Safety</h3>
  <p>Lorem ipsum damet, consecte tur adipisci do eiusmod tempo ncididunt ut labore et dolore.</p>
</div>
<div class="card active" style="left:817px;top:1200px">
  <div class="ico"><i></i><svg width="40" height="34" viewBox="0 0 40 34" fill="none" stroke="#fff" stroke-width="1.6"><rect x="6" y="4" width="14" height="12"/><rect x="20" y="16" width="14" height="12"/><path d="M20 10h6v6M14 16v6h6"/></svg></div>
  <h3>Integrity</h3>
  <p>Lorem ipsum damet, consecte tur adipisci do eiusmod tempo ncididunt ut labore et dolore.</p>
</div>
<div class="card" style="left:275px;top:1413px">
  <div class="ico"><i></i><svg width="38" height="38" viewBox="0 0 38 38" fill="none" stroke="#333" stroke-width="1.6"><circle cx="19" cy="19" r="16" stroke-dasharray="4 2"/><circle cx="19" cy="19" r="11"/><path d="M14 19l4 4 7-7"/></svg></div>
  <h3>Quality</h3>
  <p>Lorem ipsum damet, consecte tur adipisci do eiusmod tempo ncididunt ut labore et dolore.</p>
</div>
<div class="card" style="left:546px;top:1413px">
  <div class="ico"><i></i><svg width="38" height="38" viewBox="0 0 38 38" fill="none" stroke="#333" stroke-width="1.6"><circle cx="19" cy="19" r="16" stroke-dasharray="5 2"/><circle cx="19" cy="19" r="11"/><path d="M13 16h12l-6 10z M13 16l3-4h6l3 4"/></svg></div>
  <h3>Superior Service</h3>
  <p>Lorem ipsum damet, consecte tur adipisci do eiusmod tempo ncididunt ut labore et dolore.</p>
</div>
<div class="card" style="left:817px;top:1413px">
  <div class="ico"><i></i><svg width="38" height="38" viewBox="0 0 38 38" fill="none" stroke="#333" stroke-width="1.6"><circle cx="19" cy="21" r="15"/><circle cx="19" cy="19" r="4"/><path d="M12 31c1-5 4-7 7-7s6 2 7 7"/><path d="M10 8l1.5 3 3 .4-2 2 .5 3-3-1.5M28 8l-1.5 3-3 .4 2 2-.5 3 3-1.5M19 4l1 2.5h2.5l-2 1.5.8 2.5-2.3-1.5"/></svg></div>
  <h3>Customer First</h3>
  <p>Lorem ipsum damet, consecte tur adipisci do eiusmod tempo ncididunt ut labore et dolore.</p>
</div>

<!-- team -->
<h2 class="h2" style="top:1788px">OUR <span>TEAM</span></h2>
<div class="member" style="left:111px;background:linear-gradient(180deg,#5a4a3c 0%,#3a3430 55%,#1f1f22 100%)" role="img" aria-label="Portrait of team member Aron Vale"><h4>ARON VALE</h4><p>Lorem ipsum dolmet</p></div>
<div class="member" style="left:361px;background:linear-gradient(180deg,#e7e7e4 0%,#a39c8c 50%,#5a5a42 100%)" role="img" aria-label="Portrait of team member Mika Dorn"><h4>MIKA DORN</h4><p>Lorem ipsum dolmet</p></div>
<div class="member" style="left:611px;background:linear-gradient(180deg,#f1f1f1 0%,#b9b2a6 45%,#4e6a2e 100%)" role="img" aria-label="Portrait of team member Lena Shore"><h4>LENA SHORE</h4><p>Lorem ipsum dolmet</p></div>
<div class="member" style="left:862px;background:linear-gradient(180deg,#4d5e66 0%,#7a7d80 45%,#1f2a44 100%)" role="img" aria-label="Portrait of team member Tessa Quill"><h4>TESSA QUILL</h4><p>Lorem ipsum dolmet</p></div>
<div class="btn btn-teal" style="left:538px;top:2288px;width:124px;height:44px;padding-left:29px"><span>View All</span></div>

<!-- blog -->
<div class="abs blog-bg"></div>
<h2 class="h2" style="top:2452px">LATEST <span>BLOG</span></h2>
<article class="abs post-main">
  <div class="photo" role="img" aria-label="Photo of two friends smiling together indoors"></div>
  <div class="meta"><svg width="15" height="15" viewBox="0 0 16 16" fill="none" stroke="#b0b0b0" stroke-width="1.3"><rect x="1.5" y="3" width="13" height="11.5"/><path d="M1.5 6.5h13M5 1v4M11 1v4"/></svg>06/03/24</div>
  <h3>Lorem ipsum dolor sit amet, consectetur adipisc ing elit, sed do eiusmod tempor incididunt ut.</h3>
  <p>Duis aute irure dolor in reprehenderit in voluptate velit esse cill dolore eu fugiat nulla pariatur. Excepteur sint occaecat cupi</p>
</article>
<article class="post-sm" style="top:2545px"><div class="photo" style="background:linear-gradient(135deg,#c9c2b4,#6f7d8c)" role="img" aria-label="Photo of a support session at a table"></div><div class="txt">Lorem ipsum dolor sit ametr aidunt ut labore et dolore<div class="meta"><svg width="15" height="15" viewBox="0 0 16 16" fill="none" stroke="#b0b0b0" stroke-width="1.3"><rect x="1.5" y="3" width="13" height="11.5"/><path d="M1.5 6.5h13M5 1v4M11 1v4"/></svg>06/03/24</div></div></article>
<article class="post-sm" style="top:2683px"><div class="photo" style="background:linear-gradient(135deg,#3a3a36,#9aa08a)" role="img" aria-label="Photo of a child studying at a desk"></div><div class="txt">Lorem ipsum dolor sit ametr aidunt ut labore et dolore<div class="meta"><svg width="15" height="15" viewBox="0 0 16 16" fill="none" stroke="#b0b0b0" stroke-width="1.3"><rect x="1.5" y="3" width="13" height="11.5"/><path d="M1.5 6.5h13M5 1v4M11 1v4"/></svg>06/03/24</div></div></article>
<article class="post-sm" style="top:2820px"><div class="photo" style="background:linear-gradient(135deg,#4a3a30,#c7a48a)" role="img" aria-label="Photo of a parent hugging a child"></div><div class="txt">Lorem ipsum dolor sit ametr aidunt ut labore et dolore<div class="meta"><svg width="15" height="15" viewBox="0 0 16 16" fill="none" stroke="#b0b0b0" stroke-width="1.3"><rect x="1.5" y="3" width="13" height="11.5"/><path d="M1.5 6.5h13M5 1v4M11 1v4"/></svg>06/03/24</div></div></article>
<div class="btn btn-teal" style="left:538px;top:3005px;width:124px;height:44px"><span>Learn More</span></div>

<!-- footer -->
<footer class="abs footer"></footer>
<div class="abs f-brand">CALMPATH<br>SUPPORT</div>
<div class="abs social" aria-label="Social links"><span></span><span></span><span></span></div>

<div class="abs" style="left:392px;top:3161px">
  <div class="f-h">CONTACT INFO</div>
  <div class="f-col" style="margin-top:13px">
    <div class="f-row"><svg width="14" height="18" viewBox="0 0 14 18"><path fill="#00ab8e" d="M7 0a7 7 0 0 1 7 7c0 5-7 11-7 11S0 12 0 7a7 7 0 0 1 7-7z"/><circle cx="7" cy="7" r="2.5" fill="#2b2b2b"/></svg><span>Calmpath Support,<br>Address comes here</span></div>
    <div class="f-row" style="margin-top:12px"><svg width="15" height="15" viewBox="0 0 24 24"><path fill="#00ab8e" d="M6.6 10.8a15 15 0 0 0 6.6 6.6l2.2-2.2c.3-.3.7-.4 1-.2 1.1.4 2.3.6 3.6.6.6 0 1 .4 1 1V20c0 .6-.4 1-1 1A17 17 0 0 1 3 4c0-.6.4-1 1-1h3.5c.6 0 1 .4 1 1 0 1.3.2 2.5.6 3.6.1.3 0 .7-.2 1z"/></svg><span>+1800-555-0142</span></div>
    <div class="f-row" style="margin-top:7px"><svg width="15" height="12" viewBox="0 0 24 18" style="margin-top:7px"><rect x="1" y="1" width="22" height="16" fill="#00ab8e"/><path d="M1 1l11 9 11-9" stroke="#2b2b2b" stroke-width="2" fill="none"/></svg><span>hello@calmpathsupport.com</span></div>
  </div>
</div>

<div class="abs" style="left:682px;top:3161px">
  <div class="f-h">QUICK LINKS</div>
  <div class="f-col" style="margin-top:13px">Home<br>About<br>Services<br>Blog</div>
</div>

<div class="abs f-h" style="left:847px;top:3161px">SUBSCRIBE NEWSLETTER</div>
<div class="abs email-in">Email Address</div>
<div class="btn btn-teal" style="left:853px;top:3261px;width:125px;height:44px;padding-left:34px;--bar:var(--white)"><span>Submit</span></div>

<div class="abs copy">2024 Calmpath Support. All Rights Reserved.</div>

</body>
</html>
```